New Business Card Design Project

Removed as project is complete.

Target Market(s)

Industry/Entity Type

Business

Requirements
Must have
• Removed as project is complete.
Nice to have
Should not have

```html
<!DOCTYPE html>
<html lang="en">
<head>
<meta charset="utf-8">
<title>Emberline Compliance International – Business Card</title>
<link rel="stylesheet" href="https://fonts.googleapis.com/css2?family=Arimo:wght@400&display=swap">
<style>
  :root {
    --paper: #ffffff;
    --band: #231f20;
    --ink: #231f20;
    --ink-soft: #3a3a3a;
    --ember: #f2a227;
    --ember-deep: #e8711c;
  }
  * { margin: 0; padding: 0; box-sizing: border-box; }
  html, body {
    width: 1200px;
    height: 734px;
    overflow: hidden;
    background: var(--paper);
  }
  .card {
    position: relative;
    width: 1200px;
    height: 734px;
    background: var(--paper);
    font-family: "Arimo", Helvetica, Arial, sans-serif;
    color: var(--ink);
  }
  .brand-band {
    position: absolute;
    left: 0;
    top: 231px;
    width: 748px;
    height: 217px;
    background: var(--band);
  }
  .brand-mark {
    position: absolute;
    left: 118px;
    top: 282px;
    width: 112px;
    height: 112px;
    background: linear-gradient(135deg, var(--ember), var(--ember-deep));
  }
  .brand-name {
    position: absolute;
    left: 258px;
    top: 312px;
    font-size: 44px;
    font-weight: 400;
    letter-spacing: -0.5px;
    line-height: 1;
    color: var(--ember);
    white-space: nowrap;
  }
  .person {
    position: absolute;
    left: 208px;
    top: 472px;
  }
  .person-name {
    font-size: 20.5px;
    line-height: 25px;
    color: var(--ink);
  }
  .person-title {
    font-size: 19px;
    line-height: 25px;
    color: var(--ink-soft);
  }
  .contact {
    position: absolute;
    left: 208px;
    top: 554px;
    list-style: none;
    font-size: 18px;
    line-height: 23px;
    color: var(--ink-soft);
  }
  .company-address {
    position: absolute;
    left: 208px;
    top: 668px;
    font-size: 13px;
    color: var(--ink-soft);
  }
</style>
</head>
<body>
  <main class="card">
    <div class="brand-band"></div>
    <div class="brand-mark"></div>
    <div class="brand-name">Emberline Compliance</div>

    <div class="person">
      <p class="person-name">Daniel Reyes, CAMS</p>
      <p class="person-title">Director</p>
    </div>

    <ul class="contact">
      <li>+61 298 765 432</li>
      <li>DanielReyes@emberlinecompliance.com</li>
      <li>www.emberlinecompliance.com</li>
    </ul>

    <p class="company-address">Emberline Compliance International Pty Ltd, P.O. Box 2871, Glebe NSW 2037</p>
  </main>
</body>
</html>
```